Camp Brambleton "The '63 Guild"

We are looking for someone to design a bi-fold brochure that will help with our fundraising program. We are a Christian camp and retreat center. It would be a good idea to visit our website to get a feel for what we do, campbrambleton.org.

This link, https://files.example-share.net/folders/7KpQ2xVtr9LmZcW4hYbN8sDfJa3GeUoRi?usp=sharing, will provide you with pictures you can use and the text that will be needed. Don't expect all the pictures to be used, but wanted to provide some choices. The text that is provided will need to be used on the inside portion of the brochure.

Target Market(s)

Donors age range 25-70

Industry/Entity Type

Recreation

Requirements
Must have
• Text included in Google Drive. A few pictures. Brambleton Logo
Nice to have
• Professional Design
Should not have
• No clip art, no extra text (even from the website)

```html
<!DOCTYPE html>
<html lang="en">
<head>
<meta charset="utf-8">
<title>Camp Brambleton – The '63 Guild brochure</title>
<link rel="stylesheet" href="https://fonts.googleapis.com/css2?family=Playfair+Display:wght@700&family=Open+Sans:wght@400;600&display=swap">
<style>
:root{
  --bg:#e3e3e1;
  --paper:#ffffff;
  --paper-grey:#ecebe8;
  --green:#5f8f7d;
  --green-dark:#4b7666;
  --tan:#cbb99d;
  --brown:#8b7867;
  --ink:#3d3a36;
  --title:#6b5442;
  --wood-light:#e9d8bd;
  --wood-mid:#cfb28c;
  --wood-edge:#9b7a5a;
}
*{box-sizing:border-box;margin:0;padding:0}
html,body{width:1200px;height:2605px;overflow:hidden;background:var(--bg)}
body{position:relative;font-family:"Open Sans",sans-serif;color:var(--ink)}
.sheet{position:absolute;display:flex;box-shadow:0 14px 30px rgba(0,0,0,.2)}
.sheet--cover{left:390px;top:120px}
.sheet--outside{left:180px;top:960px}
.sheet--inside{left:180px;top:1830px}
.page{position:relative;width:420px;height:545px;background:var(--paper);overflow:hidden}
.page--grey{background:var(--paper-grey)}
.page svg.art{position:absolute;left:0;top:0;width:420px;height:545px}
.club-title{position:absolute;left:0;right:0;text-align:center;font-family:"Playfair Display",serif;font-weight:700;color:var(--title);font-size:27px;line-height:1}
.club-title--small{font-size:17px}
.tagline{position:absolute;left:0;right:0;text-align:center;font-family:"Playfair Display",serif;font-weight:700;color:#fff;text-transform:uppercase;letter-spacing:.5px;font-size:21px;line-height:1.2}
.url-pill{position:absolute;left:50%;transform:translateX(-50%);background:var(--tan);color:#fff;border-radius:20px;font-size:11px;font-weight:600;padding:4px 24px;white-space:nowrap;line-height:1.4}
.back-copy{position:absolute;left:40px;right:40px;top:292px;text-align:center;font-size:9px;line-height:1.5}
.back-copy .lead{color:var(--title);font-size:10px;margin-bottom:6px}
.back-copy p{margin-bottom:3px}
.book-call{position:absolute;left:0;right:0;top:388px;text-align:center;font-family:"Playfair Display",serif;font-weight:700;font-size:15px;line-height:1.2;color:var(--ink)}
.phone{position:absolute;left:0;right:0;top:410px;display:flex;justify-content:center;align-items:center;gap:6px;font-weight:600;font-size:12px;line-height:1.2}
.location{position:absolute;left:0;right:0;top:466px;text-align:center;color:#fff;font-size:9px}
.brand-mark{position:absolute;left:26px;top:262px;display:flex;align-items:center;gap:8px}
.brand-mark .dot{width:22px;height:22px;border-radius:50%;background:var(--green)}
.brand-mark .name{font-family:"Playfair Display",serif;font-weight:700;font-size:14px;color:var(--ink)}
.section-heading{position:absolute;left:26px;top:298px;font-family:"Playfair Display",serif;font-weight:700;font-size:17px;line-height:1.2;color:var(--green-dark);text-transform:uppercase}
.body-copy{position:absolute;font-size:8.6px;line-height:1.55}
.body-copy p{margin-bottom:8px}
.body-copy--left{left:26px;right:26px;top:326px}
.body-copy--right{left:34px;right:34px;top:346px}
.body-copy ul{padding-left:10px}
.body-copy li{margin-bottom:7px}
.intro{position:absolute;left:44px;right:44px;top:302px;text-align:center;font-size:11px;line-height:1.4;color:var(--ink)}
</style>
</head>
<body>

<svg width="0" height="0" style="position:absolute" aria-hidden="true">
  <defs>
    <linearGradient id="gHero" x1="0" y1="0" x2="1" y2="1">
      <stop offset="0" stop-color="#3f5530"/><stop offset=".3" stop-color="#6e7d4c"/><stop offset=".55" stop-color="#a7a077"/><stop offset=".75" stop-color="#5f6f43"/><stop offset="1" stop-color="#8d8a6a"/>
    </linearGradient>
    <linearGradient id="gC1" x1="0" y1="0" x2="1" y2="1"><stop offset="0" stop-color="#55555c"/><stop offset=".5" stop-color="#9c989a"/><stop offset="1" stop-color="#6c6a6e"/></linearGradient>
    <linearGradient id="gC2" x1="0" y1="0" x2="1" y2="1"><stop offset="0" stop-color="#f3e44a"/><stop offset=".6" stop-color="#e8c92e"/><stop offset="1" stop-color="#c9a43a"/></linearGradient>
    <linearGradient id="gC3" x1="0" y1="0" x2="1" y2="1"><stop offset="0" stop-color="#3f5d36"/><stop offset=".5" stop-color="#b8463a"/><stop offset="1" stop-color="#d7d2c8"/></linearGradient>
    <linearGradient id="gBack" x1="0" y1="0" x2="1" y2="1"><stop offset="0" stop-color="#3c3834"/><stop offset=".35" stop-color="#8e5a48"/><stop offset=".6" stop-color="#c24b3d"/><stop offset=".8" stop-color="#5c7ea0"/><stop offset="1" stop-color="#464a52"/></linearGradient>
    <linearGradient id="gIn1" x1="0" y1="0" x2="1" y2="1"><stop offset="0" stop-color="#7f2f28"/><stop offset=".35" stop-color="#6a5aa0"/><stop offset=".65" stop-color="#b7a6c6"/><stop offset="1" stop-color="#e2a0b5"/></linearGradient>
    <linearGradient id="gIn2" x1="0" y1="0" x2="1" y2="1"><stop offset="0" stop-color="#2f4a2c"/><stop offset=".4" stop-color="#3c4d82"/><stop offset=".75" stop-color="#5b6a8e"/><stop offset="1" stop-color="#c5463a"/></linearGradient>
    <linearGradient id="gC4" x1="0" y1="0" x2="1" y2="1"><stop offset="0" stop-color="#2e6a8e"/><stop offset="1" stop-color="#7aa06a"/></linearGradient>
    <linearGradient id="gC5" x1="0" y1="0" x2="1" y2="1"><stop offset="0" stop-color="#5e7d4c"/><stop offset="1" stop-color="#d2cabb"/></linearGradient>
    <linearGradient id="gArch" x1="0" y1="0" x2="1" y2="1"><stop offset="0" stop-color="#4c4c4a"/><stop offset=".5" stop-color="#a9a8a3"/><stop offset="1" stop-color="#6d6c69"/></linearGradient>
    <linearGradient id="gWood" x1="0" y1="0" x2="0" y2="1"><stop offset="0" stop-color="var(--wood-light)"/><stop offset="1" stop-color="var(--wood-mid)"/></linearGradient>
  </defs>
</svg>

<!-- Front cover -->
<div class="sheet sheet--cover">
  <div class="page">
    <svg class="art" viewBox="0 0 420 545">
      <g role="img" aria-label="Photo: children and a counselor walking together among trees at camp">
        <path d="M0 92 Q210 60 420 84 V322 Q300 392 0 352 Z" fill="url(#gHero)"/>
      </g>
      <path d="M0 352 Q300 392 420 322 V364 Q300 436 0 404 Z" fill="var(--brown)"/>
      <path d="M0 404 Q300 436 420 364 V545 H0 Z" fill="var(--green)"/>
      <path d="M90 482 Q210 466 330 474" fill="none" stroke="var(--tan)" stroke-width="0"/>
      <g role="img" aria-label="Photo: camper in costume"><circle cx="190" cy="392" r="38" fill="url(#gC1)" stroke="#fff" stroke-width="4"/></g>
      <g role="img" aria-label="Photo: campers on a yellow inflatable"><circle cx="262" cy="378" r="44" fill="url(#gC2)" stroke="#fff" stroke-width="4"/></g>
      <g role="img" aria-label="Photo: campers waving outdoors"><circle cx="332" cy="360" r="34" fill="url(#gC3)" stroke="#fff" stroke-width="4"/></g>
      <g role="img" aria-label="Carved wooden log banner behind the title"><rect x="88" y="14" width="244" height="48" rx="22" fill="url(#gWood)" stroke="var(--wood-edge)" stroke-width="2"/></g>
    </svg>
    <div class="club-title" style="top:24px">The '63 Guild</div>
    <div class="tagline" style="top:448px">Come Together @ 63 Guild</div>
    <div class="url-pill" style="top:490px">campbrambleton.org</div>
  </div>
</div>

<!-- Outside spread: back + front -->
<div class="sheet sheet--outside">
  <div class="page page--grey">
    <svg class="art" viewBox="0 0 420 545">
      <g role="img" aria-label="Photo: group of smiling boys with a counselor in front of a cabin">
        <path d="M0 0 H420 V222 Q240 252 0 214 Z" fill="url(#gBack)"/>
      </g>
      <path d="M0 440 Q220 400 420 430 V545 H0 Z" fill="var(--green)"/>
      <path d="M0 440 Q220 400 420 430" fill="none" stroke="var(--tan)" stroke-width="4"/>
      <g role="img" aria-label="Carved wooden log banner behind the title"><rect x="100" y="222" width="220" height="46" rx="21" fill="url(#gWood)" stroke="var(--wood-edge)" stroke-width="2"/></g>
    </svg>
    <div class="club-title" style="top:232px">The '63 Guild</div>
    <div class="back-copy">
      <p class="lead">We hope you'll consider joining this effort.</p>
      <p>Recurring donations can be set up at campbrambleton.org by clicking the "Give Now" button at the top of the page and selecting the subaccount "The '63 Guild."</p>
      <p>Be sure to choose your recurring date before clicking the "Submit" button. Checks can be mailed to P.O. Box 1207, Maple Falls, AR 72000.</p>
    </div>
    <div class="book-call">TO BOOK YOUR RETREAT CALL</div>
    <div class="phone">
      <svg width="14" height="14" viewBox="0 0 24 24" aria-hidden="true"><circle cx="12" cy="12" r="10.5" fill="none" stroke="var(--ink)" stroke-width="1.6"/><path d="M8.5 7.5l1.8-.4 1 2.4-1.1.9a6 6 0 0 0 3.4 3.4l.9-1.1 2.4 1-.4 1.8c-4.5.2-8.2-3.5-8-8z" fill="var(--ink)"/></svg>
      555-014-2763
    </div>
    <div class="location">Location: 48 Hollow Creek Road, Maple Falls, AR 72000</div>
    <div class="url-pill" style="top:496px">campbrambleton.org</div>
  </div>
  <div class="page">
    <svg class="art" viewBox="0 0 420 545">
      <g role="img" aria-label="Photo: children and a counselor walking together among trees at camp">
        <path d="M0 92 Q210 60 420 84 V322 Q300 392 0 352 Z" fill="url(#gHero)"/>
      </g>
      <path d="M0 352 Q300 392 420 322 V364 Q300 436 0 404 Z" fill="var(--brown)"/>
      <path d="M0 404 Q300 436 420 364 V545 H0 Z" fill="var(--green)"/>
      <g role="img" aria-label="Photo: camper in costume"><circle cx="190" cy="392" r="38" fill="url(#gC1)" stroke="#fff" stroke-width="4"/></g>
      <g role="img" aria-label="Photo: campers on a yellow inflatable"><circle cx="262" cy="378" r="44" fill="url(#gC2)" stroke="#fff" stroke-width="4"/></g>
      <g role="img" aria-label="Photo: campers waving outdoors"><circle cx="332" cy="360" r="34" fill="url(#gC3)" stroke="#fff" stroke-width="4"/></g>
      <g role="img" aria-label="Carved wooden log banner behind the title"><rect x="88" y="14" width="244" height="48" rx="22" fill="url(#gWood)" stroke="var(--wood-edge)" stroke-width="2"/></g>
    </svg>
    <div class="club-title" style="top:24px">The '63 Guild</div>
    <div class="tagline" style="top:448px">Come Together @ 63 Guild</div>
    <div class="url-pill" style="top:490px">campbrambleton.org</div>
  </div>
</div>

<!-- Inside spread -->
<div class="sheet sheet--inside">
  <div class="page page--grey">
    <svg class="art" viewBox="0 0 420 545">
      <g role="img" aria-label="Photo: group of girls smiling in front of a red cabin">
        <path d="M0 0 H420 V170 Q260 186 150 222 Q70 244 0 238 Z" fill="url(#gIn1)"/>
      </g>
      <path d="M0 238 Q70 244 150 222 Q260 186 420 170 V182 Q260 198 150 234 Q70 256 0 250 Z" fill="var(--green)"/>
      <g role="img" aria-label="Archive photo: early campers gathered outdoors"><rect x="26" y="468" width="112" height="60" fill="url(#gArch)" stroke="#fff" stroke-width="3"/></g>
      <g role="img" aria-label="Archive photo: original camp entrance"><rect x="154" y="468" width="112" height="60" fill="url(#gArch)" stroke="#fff" stroke-width="3"/></g>
      <g role="img" aria-label="Archive photo: camp founders"><rect x="282" y="468" width="112" height="60" fill="url(#gArch)" stroke="#fff" stroke-width="3"/></g>
      <rect x="0" y="537" width="420" height="8" fill="var(--green)"/>
    </svg>
    <div class="brand-mark"><span class="dot"></span><span class="name">Camp Brambleton</span></div>
    <div class="section-heading">Brambleton Summer Camp</div>
    <div class="body-copy body-copy--left">
      <p>Camp Brambleton was established in 1963 by Walter &amp; Edna Harlow and many other families to provide a place where children would have the opportunity to Encounter Christ, Community &amp; Creation. The founders of Brambleton wanted to provide a great experience at a reasonable price.</p>
      <p>We are committed to continuing that same core value. We don't believe that an incredible camp experience should only be for kids who can afford an incredible camp experience. We believe strongly that Christian Camping is a great mission field where lives are changed forever.</p>
    </div>
  </div>
  <div class="page page--grey">
    <svg class="art" viewBox="0 0 420 545">
      <g role="img" aria-label="Photo: campers and counselors in life jackets by the lake">
        <path d="M0 0 H420 V200 Q300 160 200 190 Q100 225 0 215 Z" fill="url(#gIn2)"/>
      </g>
      <path d="M0 215 Q100 225 200 190 Q300 160 420 200 V212 Q300 172 200 202 Q100 237 0 227 Z" fill="var(--tan)"/>
      <g role="img" aria-label="Photo: campers on the water"><circle cx="210" cy="178" r="32" fill="url(#gC4)" stroke="var(--green)" stroke-width="4"/></g>
      <g role="img" aria-label="Photo: smiling campers outdoors"><circle cx="272" cy="168" r="32" fill="url(#gC5)" stroke="var(--green)" stroke-width="4"/></g>
      <g role="img" aria-label="Carved wooden log banner behind the title"><rect x="140" y="258" width="140" height="32" rx="15" fill="url(#gWood)" stroke="var(--wood-edge)" stroke-width="1.5"/></g>
      <rect x="0" y="537" width="420" height="8" fill="var(--green)"/>
    </svg>
    <div class="club-title club-title--small" style="top:266px">The '63 Guild</div>
    <div class="intro">In an effort to keep camper fees at a reasonable level we established The '63 Guild.</div>
    <div class="body-copy body-copy--right">
      <ul>
        <li>It cost Brambleton just over $500 for a one-week camper and around $800 for a two-week camper. We currently charge $285 for a one-week session and $425 for a two-week session.</li>
        <li>These gaps create a significant budget shortfall each year that must be filled with both alternative revenue streams and fundraising, which makes it challenging to also raise money to make improvements to our camp facilities.</li>
      </ul>
      <p>Members of The '63 Guild are former campers, counselors and families that have been impacted by the ministry of Brambleton. They believe in the mission of Christian camping. By providing monthly support they help to defray some of the cost for campers, which allows more children to attend Brambleton each summer and facility updates.</p>
    </div>
  </div>
</div>

</body>
</html>
```